A resume/portfolio website for myself

I'm an independent software contractor, architect, tech trainer. I need a web site to present myself. Many ready to use portfolio designs are too artistic and focused on presenting design skills of the person. I like a nice website but the content should be a little less graphic than if you would present a graphic designer. Content could be presentation of me, core skill qualities and services and resume. Potentially a page with my tech courses in the longer run

```html
<!DOCTYPE html>
<html lang="en">
<head>
<meta charset="utf-8">
<title>Daniel Hartmann – Software Contractor</title>
<link href="https://fonts.googleapis.com/css2?family=Roboto:ital,wght@0,300;0,400;0,500;0,700;1,400&family=Roboto+Slab:wght@400;700&display=swap" rel="stylesheet">
<style>
:root{
  --orange:#f7941d;
  --dark:#222;
  --text:#555;
  --muted:#888;
  --line:#e4e4e4;
  --gray-bg:#efefef;
  --footer-bg:#ececec;
  --bottom-bg:#3a3a3a;
  --white:#fff;
}
*{box-sizing:border-box;margin:0;padding:0}
html,body{width:1200px;height:3600px;overflow:hidden}
body{font-family:'Roboto',Arial,sans-serif;color:var(--text);background:var(--white);font-size:14px;line-height:1.6}
.site-nav{height:70px;display:flex;align-items:center;padding:0 100px;background:var(--white);border-bottom:1px solid var(--line)}
.brand{font-size:26px;font-weight:700;color:var(--orange);margin-right:auto}
.brand span{color:var(--dark)}
.menu{display:flex;gap:28px;font-size:13px;color:var(--dark)}
.menu .active{color:var(--orange);border-bottom:2px solid var(--orange);padding-bottom:4px}
.nav-social{display:flex;gap:8px;margin-left:30px}
.dot{width:22px;height:22px;border-radius:50%;background:#555}
.hero{position:relative;height:670px;overflow:hidden}
.hero-photo{position:absolute;inset:0;background:linear-gradient(90deg,#3c3c3c 0%,#6e6e6e 45%,#a8a8a8 70%,#5a5a5a 100%)}
.hero-copy{position:absolute;left:140px;top:250px;width:560px;color:var(--white)}
.hero-copy h1{font-size:60px;font-weight:500;line-height:1.1;white-space:nowrap}
.hero-copy .role{font-size:17px;font-weight:500;margin:14px 0 10px}
.hero-copy p{font-size:13px;line-height:1.5;color:#e8e8e8;width:400px}
.btn-outline{display:inline-block;margin-top:28px;border:2px solid var(--white);border-radius:30px;padding:12px 32px;font-size:15px;color:var(--white)}
.about{height:520px;text-align:center;padding:70px 150px 0}
.about .name{font-size:28px;color:var(--orange);font-weight:500;letter-spacing:1px}
.rule{width:70px;height:2px;background:var(--orange);margin:10px auto 18px}
.about h2{font-family:'Roboto Slab',Georgia,serif;font-size:30px;font-weight:700;color:var(--dark);margin-bottom:24px}
.about p{font-size:14px;margin-bottom:18px}
.btn-solid{display:inline-block;margin-top:30px;background:var(--orange);color:var(--white);border-radius:30px;padding:14px 34px;font-size:13px;font-weight:700}
.section-title{text-align:center;font-size:34px;font-weight:500;color:var(--dark);line-height:1.3}
.work{height:1060px;background:var(--gray-bg);padding-top:60px}
.work .rule{margin-bottom:40px}
.card{background:var(--white);margin:0 140px;box-shadow:0 2px 8px rgba(0,0,0,.08)}
.timeline{position:relative;padding:45px 60px 50px}
.timeline::before{content:"";position:absolute;left:320px;top:55px;bottom:50px;width:3px;background:var(--orange)}
.job{display:flex;margin-bottom:46px;position:relative}
.job:last-child{margin-bottom:0}
.job::before{content:"";position:absolute;left:253px;top:6px;width:13px;height:13px;border-radius:50%;background:var(--white);border:3px solid var(--orange)}
.job-when{width:230px;padding-right:20px}
.job-when h4{color:var(--orange);font-size:15px;font-weight:700}
.job-when span{font-size:12px;color:var(--muted)}
.job-body{margin-left:70px;flex:1}
.job-body h3{font-size:21px;font-weight:400;color:var(--orange);margin-bottom:12px}
.job-body p{font-size:12.5px;margin-bottom:10px}
.skills{height:580px;padding-top:50px}
.skills .rule{margin-bottom:30px}
.skills .card{padding:28px 60px 34px}
.skills h3{text-align:center;color:var(--orange);font-size:22px;font-weight:400;margin-bottom:24px}
.skill-row{display:flex;justify-content:space-between}
.skill{width:250px;text-align:center}
.skill svg{display:block;margin:0 auto 14px}
.skill h4{font-size:22px;font-weight:500;color:var(--dark)}
.skill .level{font-size:13px;color:var(--muted);margin-bottom:8px}
.skill p{font-size:12.5px}
.contact{height:340px;text-align:center;padding-top:36px;border-top:1px solid var(--line)}
.contact .rule{margin-bottom:20px}
.contact blockquote{font-style:italic;font-size:14px;width:860px;margin:0 auto 16px}
.avatar{width:120px;height:120px;border-radius:50%;margin:0 auto;background:linear-gradient(#c9c9c9,#7d7d7d);border:5px solid var(--orange)}
.site-footer{height:292px;background:var(--footer-bg);display:flex;padding:60px 100px 0;gap:80px}
.site-footer h5{font-size:22px;font-weight:400;color:var(--dark);margin-bottom:20px}
.links{display:grid;grid-template-columns:160px 160px;font-size:14px;line-height:1.9}
.f-social{display:flex;gap:14px}
.f-social .dot{width:40px;height:40px}
.newsletter{margin-left:auto}
.sub-form{display:flex}
.sub-form span{width:260px;height:42px;background:var(--white);border:1px solid #ddd;font-size:13px;color:var(--muted);padding:11px 14px}
.sub-form b{background:var(--orange);color:var(--white);height:42px;padding:11px 22px;font-size:13px}
.bottom-bar{height:68px;background:var(--bottom-bg);color:#bbb;font-size:12px;display:flex;align-items:center;justify-content:center}
</style>
</head>
<body>
<nav class="site-nav">
  <div class="brand">Daniel <span>Hartmann</span></div>
  <div class="menu"><span class="active">Home</span><span>Experience</span><span>Education</span><span>Skills</span><span>Accomplishments</span><span>Portfolio</span><span>Contact</span></div>
  <div class="nav-social"><span class="dot"></span><span class="dot"></span><span class="dot"></span></div>
</nav>

<header class="hero">
  <div class="hero-photo" role="img" aria-label="Black and white portrait photograph of Daniel Hartmann"></div>
  <div class="hero-copy">
    <h1>Daniel Hartmann</h1>
    <div class="role">Software Contractor, Architect, Tech Trainer</div>
    <p>I'm an independent software contractor, architect and tech trainer. I build reliable systems, design clean architectures and teach teams to ship better software with modern tools every day.</p>
    <span class="btn-outline">Learn More Information</span>
  </div>
</header>

<section class="about">
  <div class="name">DANIEL HARTMANN</div>
  <div class="rule"></div>
  <h2>I'm an Independent Software Contractor</h2>
  <p>Contrary to popular belief, plain text is not simply random. It has roots in a piece of classical literature, making it over two thousand years old. A professor looked up one of the more obscure words and discovered the undoubtable source of it through careful study of classical literature and its many citations over time.</p>
  <p>"Sed ut perspiciatis unde omnis iste natus error sit voluptatem accusantium doloremque laudantium, totam rem aperiam, eaque ipsa quae ab illo inventore veritatis et quasi architecto beatae vitae dicta sunt explicabo. Nemo enim ipsam voluptatem quia voluptas sit aspernatur aut odit aut fugit, sed quia consequuntur magni dolores eos qui ratione voluptatem sequi nesciunt."</p>
  <span class="btn-solid">MORE ABOUT ME</span>
</section>

<section class="work">
  <h2 class="section-title">WORK EXPERIENCES</h2>
  <div class="rule"></div>
  <div class="card timeline">
    <div class="job">
      <div class="job-when"><h4>Software Contractor</h4><span>Jan 2016 - Present</span></div>
      <div class="job-body"><h3>Accusantium Doloremque</h3>
        <p>Excepteur sint occaecat cupidatat non proident, sunt in culpa qui officia.</p>
        <p>Nemo enim ipsam voluptatem quia voluptas sit aspernatur aut odit aut fugit, sed quia consequuntur magni dolores eos qui ratione voluptatem sequi nesciunt.</p></div>
    </div>
    <div class="job">
      <div class="job-when"><h4>Software Architect</h4><span>Sep 2012 - Dec 2015</span></div>
      <div class="job-body"><h3>Voluptas Assumenda Est</h3>
        <p>Temporibus autem quibusdam et aut officiis debitis aut rerum necessitatibus.</p>
        <p>On the other hand, we denounce with righteous indignation and dislike men who are so beguiled and demoralized by the charms of pleasure of the moment, so blinded by desire, that they cannot foresee the pain and trouble that are bound to ensue.</p></div>
    </div>
    <div class="job">
      <div class="job-when"><h4>Architect, Tech Trainer</h4><span>Jan 2009 - Aug 2012</span></div>
      <div class="job-body"><h3>Recusandae Voluptatibus Maiores</h3>
        <p>Ut enim ad minima veniam, quis nostrum exercitationem ullam corporis suscipit laboriosam, nisi ut aliquid ex ea commodi consequatur.</p>
        <p>In a free hour, when our power of choice is untrammelled and nothing prevents us from doing what we like best, every pleasure is to be welcomed and every pain avoided in due time.</p></div>
    </div>
    <div class="job">
      <div class="job-when"><h4>Senior Consultant</h4><span>Jun 2004 - Dec 2008</span></div>
      <div class="job-body"><h3>Deserunt Mollit Est Laborum</h3>
        <p>Neque porro quisquam est, qui dolorem ipsum quia dolor sit amet, consectetur adipisci velit.</p>
        <p>Nemo enim ipsam voluptatem quia voluptas sit aspernatur aut odit aut fugit, sed quia consequuntur magni dolores eos qui ratione voluptatem sequi nesciunt in their work.</p></div>
    </div>
  </div>
</section>

<section class="skills">
  <h2 class="section-title">PROFESSIONAL SKILLS</h2>
  <div class="rule"></div>
  <div class="card">
    <h3>Top Skills</h3>
    <div class="skill-row">
      <div class="skill">
        <svg width="150" height="150" viewBox="0 0 150 150"><circle cx="75" cy="75" r="62" fill="none" stroke="#eee" stroke-width="10"/><circle cx="75" cy="75" r="62" fill="none" stroke="#f7941d" stroke-width="10" stroke-dasharray="358 390" transform="rotate(-90 75 75)"/><text x="75" y="82" text-anchor="middle" font-size="20" fill="#f7941d" font-family="Roboto,sans-serif">92%</text></svg>
        <h4>Korvascript</h4><div class="level">Expert</div>
        <p>Building robust front end and back end applications for clients in many industries.</p>
      </div>
      <div class="skill">
        <svg width="150" height="150" viewBox="0 0 150 150"><circle cx="75" cy="75" r="62" fill="none" stroke="#eee" stroke-width="10"/><circle cx="75" cy="75" r="62" fill="none" stroke="#f7941d" stroke-width="10" stroke-dasharray="347 390" transform="rotate(-90 75 75)"/><text x="75" y="82" text-anchor="middle" font-size="20" fill="#f7941d" font-family="Roboto,sans-serif">89%</text></svg>
        <h4>Meridian, 4 years</h4><div class="level">Expert</div>
        <p>Designing large single page applications and training teams in component architecture.</p>
      </div>
      <div class="skill">
        <svg width="150" height="150" viewBox="0 0 150 150"><circle cx="75" cy="75" r="62" fill="none" stroke="#eee" stroke-width="10"/><circle cx="75" cy="75" r="62" fill="none" stroke="#f7941d" stroke-width="10" stroke-dasharray="332 390" transform="rotate(-90 75 75)"/><text x="75" y="82" text-anchor="middle" font-size="20" fill="#f7941d" font-family="Roboto,sans-serif">85%</text></svg>
        <h4>Strata, 4 years</h4><div class="level">Advanced</div>
        <p>Writing typed, maintainable code bases and teaching best practices to developers.</p>
      </div>
    </div>
  </div>
</section>

<section class="contact">
  <h2 class="section-title">GET IN TOUCH</h2>
  <div class="rule"></div>
  <blockquote>"At vero eos et accusamus et iusto odio dignissimos ducimus qui blanditiis praesentium voluptatum deleniti atque corrupti quos dolores et quas molestias excepturi sint occaecati cupiditate non provident, similique sunt in culpa qui officia deserunt mollitia animi."</blockquote>
  <div class="avatar" role="img" aria-label="Round portrait photo of Daniel Hartmann"></div>
</section>

<footer class="site-footer">
  <div><h5>Quick Links</h5>
    <div class="links"><span>Experience</span><span>Accomplishments</span><span>Education</span><span>Portfolio</span><span>Skills</span><span>Contact</span></div></div>
  <div><h5>Get Social</h5><div class="f-social"><span class="dot"></span><span class="dot"></span><span class="dot"></span></div></div>
  <div class="newsletter"><h5>Join Our Newsletter</h5><div class="sub-form"><span>Email</span><b>SUBMIT</b></div></div>
</footer>
<div class="bottom-bar">Copyright © 2024 Daniel Hartmann. All rights reserved. Terms of Use | Privacy Policy</div>
</body>
</html>
```